BrindleStaffing Business Card Design

We are a staffing company finding positions for dedicated nurses and physicians.

Target Market(s)

Business Professionals

Industry/Entity Type

Staffing

Contact Information for Business Card

Gordon Pratley
Chairman
417 39th Avenue South
SAINT PETERSBURG FL 33712
813-555-4172 Mobile
813-555-8036 Fax
gpratley@brindlestaffing.com
www.brindlestaffing.com

Font styles to use
Sans Serif

Colors
fbee3e
f04a50
f37122

Requirements
Must have
• Logo Attached, see colors below. We'd like to see Yellow, Orange and Red.

```html
<!DOCTYPE html>
<html lang="en">
<head>
<meta charset="utf-8">
<title>BrindleStaffing Business Card</title>
<link href="https://fonts.googleapis.com/css2?family=Poppins:wght@400;500;600;700&display=swap" rel="stylesheet">
<style>
  :root {
    --backdrop: #7b7b7b;
    --brand-yellow: #fbee3e;
    --brand-red: #f04a50;
    --brand-orange: #f37122;
    --ink: #1d1d1d;
    --paper: #ffffff;
    --rule: #222222;
  }
  * { margin: 0; padding: 0; box-sizing: border-box; }
  html, body { width: 1200px; height: 895px; overflow: hidden; }
  body {
    background: var(--backdrop);
    font-family: "Poppins", Arial, sans-serif;
    position: relative;
  }
  .card {
    position: absolute;
    width: 540px;
    height: 309px;
    border-radius: 22px;
    overflow: hidden;
    box-shadow: 0 6px 18px rgba(0,0,0,0.35);
  }

  /* Back side */
  .card-back {
    left: 80px; top: 100px;
    background: var(--brand-orange);
    color: var(--paper);
  }
  .card-back .wordmark {
    position: absolute;
    top: 104px; left: 0; right: 0;
    text-align: center;
    font-weight: 600;
    font-size: 54px;
    letter-spacing: -1px;
  }
  .card-back .web-rule {
    position: absolute;
    left: 0; right: 0; bottom: 48px;
    display: flex; align-items: center; gap: 14px;
  }
  .card-back .web-rule::before,
  .card-back .web-rule::after {
    content: ""; flex: 1; height: 1px; background: var(--brand-yellow);
  }
  .card-back .web-rule span { font-size: 13px; letter-spacing: 2px; }

  /* Front side */
  .card-front {
    left: 580px; top: 470px;
    background: var(--paper);
    color: var(--ink);
    border-bottom: 7px solid var(--brand-yellow);
  }
  .card-front .wordmark {
    position: absolute;
    top: 40px; left: 34px;
    font-weight: 600;
    font-size: 38px;
    letter-spacing: -1px;
    color: var(--brand-orange);
  }
  .card-front .address {
    position: absolute;
    top: 100px; right: 28px;
    text-align: right;
    font-style: normal;
    font-size: 12.5px;
    line-height: 1.45;
  }
  .card-front .address-rule {
    position: absolute;
    top: 94px; right: 24px;
    width: 250px; height: 1px; background: var(--rule);
  }
  .card-front .identity {
    position: absolute;
    left: 0; top: 142px;
    padding-left: 34px;
    border-left: 12px solid var(--brand-red);
  }
  .card-front .identity .person {
    font-weight: 600; font-size: 28px; line-height: 1.1;
  }
  .person .first { color: var(--brand-red); }
  .person .last { color: var(--brand-orange); }
  .card-front .identity .role { font-size: 14px; }
  .card-front .contact-rule {
    position: absolute;
    left: 46px; top: 202px;
    width: 300px; height: 1px; background: var(--rule);
  }
  .card-front .contacts {
    position: absolute;
    left: 46px; top: 209px;
    list-style: none;
    font-size: 13.5px;
    line-height: 20px;
  }
  .contacts li { display: flex; align-items: center; gap: 10px; }
  .contacts svg { width: 12px; height: 12px; fill: var(--brand-red); }
</style>
</head>
<body>

<section class="card card-back">
  <div class="wordmark">BrindleStaffing</div>
  <div class="web-rule"><span>www.brindlestaffing.com</span></div>
</section>

<section class="card card-front">
  <div class="wordmark">BrindleStaffing</div>

  <div class="address-rule"></div>
  <address class="address">417 39th Avenue South<br>SAINT PETERSBURG FL 33712</address>

  <div class="identity">
    <div class="person"><span class="first">Gordon</span> <span class="last">Pratley</span></div>
    <div class="role">Chairman</div>
  </div>
  <div class="contact-rule"></div>

  <ul class="contacts">
    <li>
      <svg viewBox="0 0 24 24" aria-hidden="true"><path d="M6.6 10.8a15.1 15.1 0 0 0 6.6 6.6l2.2-2.2c.3-.3.7-.4 1-.2 1.1.4 2.3.6 3.6.6.6 0 1 .4 1 1V20c0 .6-.4 1-1 1C10.6 21 3 13.4 3 4c0-.6.4-1 1-1h3.5c.6 0 1 .4 1 1 0 1.3.2 2.5.6 3.6.1.3 0 .7-.2 1z"/></svg>
      813-555-4172 Mobile
    </li>
    <li>
      <svg viewBox="0 0 24 24" aria-hidden="true"><path d="M6 2h12v6H6z M3 9h18v9h-3v4H6v-4H3z M8 15v5h8v-5z"/></svg>
      813-555-8036 Fax
    </li>
    <li>
      <svg viewBox="0 0 24 24" aria-hidden="true"><path d="M2 5h20v14H2z M2 5l10 8 10-8"/></svg>
      gpratley@brindlestaffing.com
    </li>
    <li>
      <svg viewBox="0 0 24 24" aria-hidden="true"><circle cx="12" cy="12" r="10"/></svg>
      www.brindlestaffing.com
    </li>
  </ul>
</section>

</body>
</html>
```